KBT Business Cards

We require business cards for our business. We would like a matte black back to the card, with our logo centred in the middle. The front side of the card is open to design.

Target Market(s)

Clients looking for legal services (professional)

Industry/Entity Type

Legal

Contact Information for Business Card

Doran Kelbrath
Partner
Mobile: 0461 738 524
Email: doran@kbtlaw.co
Website: www.kbtlaw.co
Level 3, 118 Wendmore Street
Sydney NSW 2000

Font styles to use
Other font styles liked:
• Avenir

Colors
f04a50
ffffff
1b1b1b

Requirements
Must have
• Black back with logo included in the centre of the card.
• Our font is Avenir.

```html
<!DOCTYPE html>
<html lang="en">
<head>
<meta charset="utf-8">
<title>KBT Business Cards</title>
<link rel="stylesheet" href="https://fonts.googleapis.com/css2?family=Fira+Sans:wght@400;600;700&display=swap">
<style>
  :root {
    --stage: #2b2b2d;
    --crimson: #d0234f;
    --matte: #1b1b1b;
    --matte-light: #262626;
    --paper: #ffffff;
    --ink: #1b1b1b;
    --text: #222222;
  }
  * { box-sizing: border-box; margin: 0; padding: 0; }
  html, body {
    width: 1200px; height: 900px; overflow: hidden;
    background: var(--stage);
    font-family: "Fira Sans", "Avenir", sans-serif;
  }
  .stage { position: relative; width: 1200px; height: 900px; }
  .card {
    position: absolute; left: 290px; width: 620px; height: 354px;
    box-shadow: 0 14px 30px rgba(0,0,0,0.5);
  }
  .card--brand {
    top: 48px;
    background: radial-gradient(ellipse at 50% 45%, var(--matte-light) 0%, var(--matte) 70%);
    display: flex; align-items: center; justify-content: center;
  }
  .brand-lockup { display: flex; align-items: center; gap: 26px; }
  .brand-square { width: 80px; height: 80px; background: var(--crimson); flex: none; }
  .brand-name {
    color: var(--paper); font-weight: 700; font-size: 32px;
    line-height: 1.04; letter-spacing: 0.5px; text-transform: uppercase;
  }
  .card--contact { top: 470px; background: var(--paper); }
  .contact-tab {
    position: absolute; left: 0; top: 24px; width: 26px; height: 48px;
    background: var(--ink);
  }
  .holder-name {
    position: absolute; left: 48px; top: 22px;
    color: var(--crimson); font-weight: 700; font-size: 26px; letter-spacing: 0.8px;
    text-transform: uppercase; line-height: 1.2;
  }
  .holder-role {
    position: absolute; left: 48px; top: 56px;
    color: var(--text); font-size: 15px; letter-spacing: 0.3px;
  }
  .contact-list {
    position: absolute; left: 48px; top: 196px; list-style: none;
    color: var(--ink); font-size: 19px;
  }
  .contact-list li { display: flex; align-items: center; gap: 14px; height: 28px; }
  .contact-list svg { width: 18px; height: 18px; fill: var(--crimson); flex: none; }
  .address {
    position: absolute; left: 48px; top: 290px;
    color: var(--ink); font-size: 19px; line-height: 1.3; font-style: normal;
  }
</style>
</head>
<body>
<main class="stage">
  <section class="card card--brand" aria-label="Card back">
    <div class="brand-lockup">
      <span class="brand-square" aria-hidden="true"></span>
      <p class="brand-name">Kelbrath<br>Barne Tollan<br>Legal</p>
    </div>
  </section>

  <section class="card card--contact" aria-label="Card front">
    <span class="contact-tab" aria-hidden="true"></span>
    <h1 class="holder-name">Doran Kelbrath</h1>
    <p class="holder-role">Partner</p>
    <ul class="contact-list">
      <li>
        <svg viewBox="0 0 24 24" aria-hidden="true"><path d="M6.6 10.8a15 15 0 0 0 6.6 6.6l2.2-2.2c.3-.3.7-.4 1-.2 1.1.4 2.3.6 3.6.6.6 0 1 .4 1 1V20c0 .6-.4 1-1 1A17 17 0 0 1 3 4c0-.6.4-1 1-1h3.5c.6 0 1 .4 1 1 0 1.3.2 2.5.6 3.6.1.3 0 .7-.2 1z"/></svg>
        0461 738 524
      </li>
      <li>
        <svg viewBox="0 0 24 24" aria-hidden="true"><path d="M2 5h20v14H2z"/><path d="M3 6l9 7 9-7" fill="none" stroke="#fff" stroke-width="1.6"/></svg>
        doran@kbtlaw.co
      </li>
      <li>
        <svg viewBox="0 0 24 24" aria-hidden="true"><circle cx="12" cy="12" r="10"/><path d="M2 12h20M12 2c3 3 3 17 0 20M12 2c-3 3-3 17 0 20" fill="none" stroke="#fff" stroke-width="1.4"/></svg>
        www.kbtlaw.co
      </li>
    </ul>
    <address class="address">Level 3, 118 Wendmore Street<br>Sydney NSW 2000</address>
  </section>
</main>
</body>
</html>
```